Corvel Capital LLC

Need Professional Business cards for New Investment Fund

Target Market(s)

High Quality investors

Industry/Entity Type

Financial

Contact Information for Business Card

Phone Number +1 555 284 6190
Name Lukas Varenko
Title Fund Manager
email lv@FundTalvren.com
Website www.FundTalvren.com

Colors

Designer to choose colors to be used in the design.

Requirements
Must have
• Must have our Logo and all of the above. Must be made so lettering and loge can be raised

```html
<!DOCTYPE html>
<html lang="en">
<head>
<meta charset="utf-8">
<title>Talvren Capital – Business Cards</title>
<link rel="stylesheet" href="https://fonts.googleapis.com/css2?family=Jost:wght@500&family=Roboto:wght@400;500;700&display=swap">
<style>
  :root {
    --backdrop: #c9c9c8;
    --forest: #39443c;
    --lime: #8dbf1e;
    --paper: #f1f1f0;
    --ink: #39443c;
    --mist: #eeeeec;
  }
  html, body {
    margin: 0;
    padding: 0;
    width: 1200px;
    height: 1138px;
    overflow: hidden;
    background: var(--backdrop);
  }
  .card {
    position: absolute;
    width: 620px;
    height: 374px;
    border-radius: 16px;
    box-sizing: border-box;
  }
  .card--front {
    left: 274px;
    top: 186px;
    background: var(--forest);
  }
  .card--back {
    left: 276px;
    top: 608px;
    background: var(--paper);
  }
  .brand {
    position: absolute;
    display: flex;
    align-items: center;
    font-family: "Jost", sans-serif;
    font-weight: 500;
    letter-spacing: 1px;
    white-space: nowrap;
  }
  .brand__mark {
    display: block;
    background: var(--lime);
  }
  .card--front .brand {
    left: 50%;
    top: 50%;
    transform: translate(-50%, -50%);
    gap: 16px;
    font-size: 60px;
    color: var(--mist);
  }
  .card--front .brand__mark { width: 34px; height: 34px; }
  .card--back .brand {
    left: 26px;
    top: 62px;
    gap: 10px;
    font-size: 36px;
    color: var(--ink);
  }
  .card--back .brand__mark { width: 22px; height: 22px; }
  .accent-block {
    position: absolute;
    left: 428px;
    top: 124px;
    width: 128px;
    height: 128px;
    background: var(--lime);
  }
  .holder {
    position: absolute;
    left: 26px;
    top: 196px;
    font-family: "Roboto", sans-serif;
    color: var(--ink);
  }
  .holder__name {
    margin: 0;
    font-size: 22px;
    font-weight: 700;
    line-height: 26px;
  }
  .holder__title {
    margin: 6px 0 0;
    font-size: 15px;
    font-weight: 400;
  }
  .contacts {
    position: absolute;
    left: 26px;
    top: 274px;
    margin: 0;
    padding: 0;
    list-style: none;
    font-family: "Roboto", sans-serif;
    font-size: 16px;
    color: var(--ink);
  }
  .contacts li {
    display: flex;
    align-items: center;
    height: 24px;
    white-space: nowrap;
  }
  .contacts svg {
    width: 14px;
    height: 14px;
    margin-right: 17px;
    fill: var(--lime);
  }
</style>
</head>
<body>
  <section class="card card--front">
    <div class="brand"><span class="brand__mark"></span>Talvren</div>
  </section>

  <section class="card card--back">
    <div class="brand"><span class="brand__mark"></span>Talvren</div>
    <span class="accent-block"></span>

    <div class="holder">
      <h1 class="holder__name">Lukas Varenko</h1>
      <p class="holder__title">Fund Manager</p>
    </div>

    <ul class="contacts">
      <li>
        <svg viewBox="0 0 16 16" aria-hidden="true"><path d="M2 5c0-2 2-3 6-3s6 1 6 3v1h-3V5H5v1H2z"/><path d="M4 8l2-2h4l2 2v6H4z"/></svg>
        +1 555 284 6190
      </li>
      <li>
        <svg viewBox="0 0 16 16" aria-hidden="true"><path d="M1 3h14v1L8 9 1 4z"/><path d="M1 6l7 5 7-5v7H1z"/></svg>
        lv@FundTalvren.com
      </li>
      <li>
        <svg viewBox="0 0 16 16" aria-hidden="true"><circle cx="8" cy="8" r="7"/><path d="M1 8h14M8 1c-3 3-3 11 0 14M8 1c3 3 3 11 0 14" stroke="#f1f1f0" stroke-width="1" fill="none"/></svg>
        www.FundTalvren.com
      </li>
    </ul>
  </section>
</body>
</html>
```